Copperleaf Roofing Business Card

This is my current business card. But I’d like to make some changes. Somewhere on the card I’d like to list some of the services we offer. Maybe on the back? But I’d still like to keep the red. White and black modern look.

-residential & commercial roofing
-Roof Repairs & Maintenance
-Storm Damage & Insurance Claims specialist
-Christmas Lights and permanent Christmas lights
Fencing. Windows. Gutters. Siding. Sheetrock, painting.

```html
<!DOCTYPE html>
<html lang="en">
<head>
<meta charset="utf-8">
<title>Copperleaf Roofing Business Card</title>
<link href="https://fonts.googleapis.com/css2?family=Michroma&family=Arimo:wght@400;700&display=swap" rel="stylesheet">
<style>
  :root {
    --bg: #3d3d3d;
    --card-white: #ffffff;
    --card-dark: #2c2c2c;
    --red: #e0141b;
    --red-deep: #a10d12;
    --ink: #1a1a1a;
    --grey: #777777;
    --light: #f2f2f2;
    --muted: #c9c9c9;
  }
  * { margin: 0; padding: 0; box-sizing: border-box; }
  html, body {
    width: 1200px; height: 803px; overflow: hidden;
    background: var(--bg);
  }
  .stage {
    width: 1200px; height: 803px;
    display: flex; align-items: center; justify-content: center; gap: 56px;
  }
  .card {
    width: 525px; height: 300px;
    border-radius: 20px;
    position: relative;
    overflow: hidden;
    border-bottom: 4px solid var(--red);
  }
  .card--front { background: var(--card-white); }
  .card--back { background: var(--card-dark); }

  /* front */
  .brand {
    position: absolute; top: 44px; right: 44px;
    display: flex; align-items: center; gap: 14px;
  }
  .brand-dot {
    width: 58px; height: 58px; border-radius: 50%;
    background: var(--red);
  }
  .brand-name {
    font-family: "Michroma", sans-serif;
    font-size: 20px; line-height: 1.25;
    color: var(--red);
    letter-spacing: 0.02em;
  }
  .contact {
    position: absolute; left: 40px; bottom: 36px;
  }
  .person-name {
    font-family: "Michroma", sans-serif;
    font-size: 22px; font-weight: 400; color: var(--red);
    letter-spacing: 0.04em;
  }
  .person-role {
    font-family: "Arimo", sans-serif;
    font-size: 13px; color: var(--grey);
    margin: 2px 0 16px;
  }
  .contact-list { list-style: none; }
  .contact-item {
    display: flex; align-items: center; gap: 10px;
    font-family: "Arimo", sans-serif;
    font-size: 14px; color: var(--ink);
    line-height: 1.45;
  }
  .contact-icon { width: 13px; height: 13px; flex: none; }

  /* back */
  .back-brand {
    position: absolute; top: 26px; left: 0; width: 100%;
    display: flex; align-items: center; justify-content: center; gap: 14px;
  }
  .back-circle {
    width: 52px; height: 52px; border-radius: 50%;
    background: var(--red);
    flex: none;
  }
  .back-name {
    font-family: "Michroma", sans-serif;
    font-size: 17px; color: var(--light);
    letter-spacing: 0.03em;
    white-space: nowrap;
  }
  .services {
    position: absolute; top: 100px; left: 60px; right: 60px;
    border-top: 1px solid var(--red);
    padding-top: 12px;
    list-style: none;
  }
  .service {
    display: flex; align-items: center; gap: 10px;
    font-family: "Arimo", sans-serif;
    font-size: 13px; color: var(--light);
    line-height: 1.7;
    white-space: nowrap;
  }
  .service::before {
    content: ""; width: 7px; height: 7px; flex: none;
    background: var(--red);
  }
  .back-web {
    position: absolute; bottom: 18px; width: 100%; text-align: center;
    font-family: "Arimo", sans-serif;
    font-size: 14px; color: var(--muted);
  }
</style>
</head>
<body>
<main class="stage">
  <section class="card card--front">
    <div class="brand">
      <div class="brand-dot"></div>
      <div class="brand-name">COPPERLEAF<br>ROOFING CO.</div>
    </div>
    <div class="contact">
      <h1 class="person-name">DALE MERCER</h1>
      <p class="person-role">Roofing Contractor in texas</p>
      <ul class="contact-list">
        <li class="contact-item">
          <svg class="contact-icon" viewBox="0 0 24 24"><path fill="#e0141b" d="M6.6 10.8a15 15 0 0 0 6.6 6.6l2.2-2.2c.3-.3.7-.4 1-.2 1.1.4 2.3.6 3.6.6.6 0 1 .4 1 1V20c0 .6-.4 1-1 1A17 17 0 0 1 3 4c0-.6.4-1 1-1h3.5c.6 0 1 .4 1 1 0 1.3.2 2.5.6 3.6.1.3 0 .7-.2 1z"/></svg>
          555.014.2283
        </li>
        <li class="contact-item">
          <svg class="contact-icon" viewBox="0 0 24 24"><rect x="2" y="5" width="20" height="14" rx="2" fill="#e0141b"/><path d="M3 6l9 7 9-7" fill="none" stroke="#fff" stroke-width="2"/></svg>
          dale@copperleafroofing.co
        </li>
        <li class="contact-item">
          <svg class="contact-icon" viewBox="0 0 24 24"><circle cx="12" cy="12" r="10" fill="#e0141b"/><path d="M2 12h20M12 2c3 3 3 17 0 20M12 2c-3 3-3 17 0 20" fill="none" stroke="#fff" stroke-width="1.6"/></svg>
          www.copperleafroofing.co
        </li>
      </ul>
    </div>
  </section>

  <section class="card card--back">
    <div class="back-brand">
      <div class="back-circle"></div>
      <div class="back-name">COPPERLEAF ROOFING CO.</div>
    </div>
    <ul class="services">
      <li class="service">Residential &amp; Commercial Roofing</li>
      <li class="service">Roof Repairs &amp; Maintenance</li>
      <li class="service">Storm Damage &amp; Insurance Claims Specialist</li>
      <li class="service">Christmas Lights &amp; Permanent Christmas Lights</li>
      <li class="service">Fencing · Windows · Gutters · Siding · Sheetrock · Painting</li>
    </ul>
    <p class="back-web">www.copperleafroofing.co</p>
  </section>
</main>
</body>
</html>
```